Business Card Design For Marketing Agnecy LVP

Need business card design for marketing agency.

Doug Fenwick
President, CEO
1-555-302-4196
doug@boldpromoperksgroup.example
www.BoldPromoPerksGroup.example

Back Side:
Boost Sales Using Rewards, Incentives & Giveaways
Get A Free Sample Package

Target Market(s)

B2B

Industry/Entity Type

Marketing

Contact Information for Business Card

Doug Fenwick
President, CEO
1-555-302-4196

Back Side:
Get A Free Sample Package

Please note that my current url is OLD DESIGN. I am working on new design and want the business card to match color themes at least on new site. Here is the demo link for new site so you can see the colors I use, etc.

http://layoutcratehub.example/kq/doug/lvp_final/index.html

Requirements
Must have
• Please note that my current url is OLD DESIGN. I am working on new design and want the business card to match color themes at least on new site. Here is the demo link for new site so you can see the colors I use, etc.

Nice to have

Should not have

```html
<!DOCTYPE html>
<html lang="en">
<head>
<meta charset="utf-8">
<title>LVP Business Card</title>
<link rel="stylesheet" href="https://fonts.googleapis.com/css2?family=Montserrat:wght@400;700&family=Roboto:wght@400;500;700&display=swap">
<style>
  :root {
    --brand-blue: #0f77be;
    --ink-grey: #58595b;
    --paper: #ffffff;
    --backdrop: #c6cacd;
  }
  * { box-sizing: border-box; margin: 0; padding: 0; }
  html, body {
    width: 1200px; height: 1018px; overflow: hidden;
    background: var(--backdrop);
  }
  .card {
    position: absolute; top: 181px;
    width: 374px; height: 656px;
  }
  .card--front { left: 190px; background: var(--paper); }
  .card--back  { left: 648px; background: var(--brand-blue); }

  .wordmark {
    position: absolute; left: 0; right: 0;
    display: flex; flex-direction: column; align-items: center;
    font-family: "Montserrat", sans-serif; font-weight: 700;
  }
  .card--front .wordmark { top: 66px; color: var(--brand-blue); }
  .card--back  .wordmark { top: 186px; color: var(--paper); }
  .wordmark__initials { font-size: 86px; line-height: 1; letter-spacing: 1px; }
  .card--back .wordmark__initials { font-size: 102px; }
  .wordmark__name {
    margin-top: 8px; font-size: 9.5px; letter-spacing: 1.4px;
    padding-top: 5px; border-top: 1.5px solid currentColor;
    white-space: nowrap;
  }
  .card--back .wordmark__name { font-size: 11px; letter-spacing: 1.7px; }

  .contact {
    position: absolute; left: 33px; top: 470px;
    font-family: "Roboto", sans-serif; color: var(--ink-grey);
  }
  .contact__name { font-size: 21px; font-weight: 700; color: var(--brand-blue); letter-spacing: 0.2px; }
  .contact__role { font-size: 16px; margin-top: 4px; }
  .contact__rule { width: 11px; height: 2px; background: var(--brand-blue); margin: 11px 0 14px; }
  .contact__list { list-style: none; }
  .contact__item {
    display: flex; align-items: center; gap: 5px;
    font-size: 15.5px; height: 22.8px;
  }
  .contact__item svg { width: 11px; height: 11px; fill: var(--brand-blue); flex: none; }

  .pitch {
    position: absolute; left: 0; right: 0; top: 514px;
    text-align: center; color: var(--paper);
  }
  .pitch__lines {
    list-style: none; font-family: "Montserrat", sans-serif;
    font-size: 13.5px; letter-spacing: 0.4px; line-height: 22.5px;
  }
  .pitch__rule {
    width: 263px; margin: 10px auto 0;
    border-top: 1px dashed rgba(255,255,255,0.85);
  }
  .pitch__url { font-family: "Roboto", sans-serif; font-size: 16px; margin-top: 7px; }
</style>
</head>
<body>
  <section class="card card--front" aria-label="Card front">
    <div class="wordmark">
      <span class="wordmark__initials">LVP</span>
      <span class="wordmark__name">BOLD PROMO PERKS GROUP</span>
    </div>

    <div class="contact">
      <h1 class="contact__name">DOUG FENWICK</h1>
      <p class="contact__role">President, CEO</p>
      <div class="contact__rule"></div>
      <ul class="contact__list">
        <li class="contact__item">
          <svg viewBox="0 0 24 24" aria-hidden="true"><path d="M6.6 10.8a15.1 15.1 0 0 0 6.6 6.6l2.2-2.2c.3-.3.7-.4 1-.2 1.1.4 2.3.6 3.6.6.6 0 1 .4 1 1V20c0 .6-.4 1-1 1A17 17 0 0 1 3 4c0-.6.4-1 1-1h3.5c.6 0 1 .4 1 1 0 1.3.2 2.5.6 3.6.1.3 0 .7-.2 1l-2.3 2.2z"/></svg>
          1-555-302-4196
        </li>
        <li class="contact__item">
          <svg viewBox="0 0 24 24" aria-hidden="true"><path d="M2 5h20v14H2z M3.5 6.5l8.5 7 8.5-7" stroke="#fff" stroke-width="1.6"/></svg>
          doug@boldpromoperksgroup.example
        </li>
        <li class="contact__item">
          <svg viewBox="0 0 24 24" aria-hidden="true"><circle cx="12" cy="12" r="10"/><path d="M2 12h20M12 2c3 3 3 17 0 20M12 2c-3 3-3 17 0 20" stroke="#fff" stroke-width="1.4" fill="none"/></svg>
          www.BoldPromoPerksGroup.example
        </li>
      </ul>
    </div>
  </section>

  <section class="card card--back" aria-label="Card back">
    <div class="wordmark">
      <span class="wordmark__initials">LVP</span>
      <span class="wordmark__name">BOLD PROMO PERKS GROUP</span>
    </div>

    <div class="pitch">
      <ul class="pitch__lines">
        <li>Incentives &amp; Giveaways</li>
        <li>Boost Sales Using Rewards</li>
        <li>Get A Free Sample Package</li>
      </ul>
      <div class="pitch__rule"></div>
      <p class="pitch__url">www.BoldPromoPerksGroup.example</p>
    </div>
  </section>
</body>
</html>
```